Marrowby Water Taxi and Transport Business Card

I need business cards for my new water taxi and freight transport business I have started here in Kodiak Alaska. Kodiak is a remote island in the middle of the gulf of Alaska. There are seven native villages around the island and Kodiak is the #2 fishing port in the United States. We also have the largest Coast Guard Base in the U.S. My company will be providing water taxi and freight transport logistics to the villages and many hunting and fishing lodges as well as remote properties around the island.

I would like a business card that isn't status quo, something that stands out, either in feel or appearance. I do like clean minimal designs but it needs to have the necessary contact info on it.

Target Market(s)

remote lodge / property owners, residents of the many villages around Kodiak and any one wanting to enjoy the great outdoors of Kodiak Alaska

Industry/Entity Type

Business

Contact Information for Business Card

I like clean simple designs that aren't cluttered but still provide the necessary information

Colors
0255a3
3277b5
33a4d5
9bcb3c
add136
fbed22
ffc214
f78f20
f37122

Requirements
Must have
• logo and contact info
• Captain Mason Elwick
• www.marrowbyferryline.com
• mason@marrowbyferryline.com

```html
<!DOCTYPE html>
<html lang="en">
<head>
<meta charset="UTF-8">
<title>Marrowby Water Taxi and Transport – Business Card</title>
<link href="https://fonts.googleapis.com/css2?family=Mulish:wght@400;600;700;800&display=swap" rel="stylesheet">
<style>
  :root {
    --page-bg: #e9e9e6;
    --card-white: #ffffff;
    --card-black: #050505;
    --navy: #0255a3;
    --mid-blue: #3277b5;
    --sky: #33a4d5;
    --orange: #f78f20;
    --ink: #2b2b2b;
    --shadow: rgba(0,0,0,0.28);
  }
  * { box-sizing: border-box; margin: 0; padding: 0; }
  html, body {
    width: 1200px; height: 1000px; overflow: hidden;
    background: var(--page-bg);
    font-family: "Mulish", "Helvetica Neue", Arial, sans-serif;
  }
  .card {
    position: absolute;
    left: 265px;
    width: 665px; height: 397px;
    border-radius: 22px;
    overflow: hidden;
    box-shadow: 0 6px 16px var(--shadow);
  }
  .card--front { top: 73px; background: var(--card-white); }
  .card--back { top: 533px; background: var(--card-black); }

  .brand { position: absolute; text-align: center; }
  .card--front .brand { left: 40px; top: 150px; width: 300px; }
  .card--back .brand { left: 165px; top: 170px; width: 335px; }
  .brand__dot {
    display: block; margin: 0 auto 14px;
    width: 38px; height: 38px; border-radius: 50%;
    background: var(--orange);
  }
  .brand__name {
    display: block;
    font-weight: 800; color: var(--navy);
    font-size: 52px; line-height: 1; letter-spacing: 1px;
    text-transform: uppercase;
  }
  .brand__tagline {
    display: block;
    font-weight: 800; color: var(--navy);
    font-size: 19px; line-height: 1.5;
  }
  .card--back .brand__name,
  .card--back .brand__tagline { color: var(--mid-blue); }

  .contact { position: absolute; left: 391px; top: 114px; }
  .contact__name {
    font-weight: 800; font-size: 22px; color: var(--navy);
    line-height: 1.2;
  }
  .contact__role { font-size: 15px; color: var(--ink); margin-top: 2px; }
  .contact__list { list-style: none; margin-top: 38px; }
  .contact__item {
    display: flex; align-items: center; gap: 9px;
    font-size: 15px; color: var(--ink); height: 28px;
  }
  .contact__icon { width: 15px; height: 15px; flex: none; }

  .wave { position: absolute; left: 0; bottom: 0; width: 665px; height: 100px; }
</style>
</head>
<body>

<section class="card card--front" aria-label="Business card front">
  <div class="brand">
    <span class="brand__dot"></span>
    <span class="brand__name">Marrowby</span>
    <span class="brand__tagline">Water Taxi and Transport</span>
  </div>

  <div class="contact">
    <p class="contact__name">Mason Elwick</p>
    <p class="contact__role">Captain</p>
    <ul class="contact__list">
      <li class="contact__item">
        <svg class="contact__icon" viewBox="0 0 16 16" aria-hidden="true">
          <rect x="1" y="3" width="14" height="10" rx="1" fill="#f78f20"/>
          <path d="M1.5 3.8 L8 9 L14.5 3.8" fill="none" stroke="#fff" stroke-width="1.3"/>
        </svg>
        mason@marrowbyferryline.com
      </li>
      <li class="contact__item">
        <svg class="contact__icon" viewBox="0 0 16 16" aria-hidden="true">
          <circle cx="7" cy="7" r="5.5" fill="none" stroke="#f78f20" stroke-width="1.8"/>
          <path d="M8 7 L15 10 L12 11 L14 14.5 L12.8 15 L11 12 L9 14 Z" fill="#f78f20"/>
        </svg>
        www.marrowbyferryline.com
      </li>
    </ul>
  </div>

  <svg class="wave" viewBox="0 0 665 100" preserveAspectRatio="none" aria-hidden="true">
    <path d="M0 55 C120 80 230 85 380 55 C480 35 580 25 665 22 L665 100 L0 100 Z" fill="#0255a3"/>
    <path d="M0 64 C120 88 240 92 390 62 C490 42 585 34 665 32 L665 100 L0 100 Z" fill="#ffffff"/>
    <path d="M0 72 C130 94 250 98 400 72 C500 52 590 44 665 42 L665 100 L0 100 Z" fill="#33a4d5"/>
  </svg>
</section>

<section class="card card--back" aria-label="Business card back">
  <div class="brand">
    <span class="brand__dot"></span>
    <span class="brand__name">Marrowby</span>
    <span class="brand__tagline">Water Taxi and Transport</span>
  </div>
</section>

</body>
</html>
```